Logo and Card design for KRV Home Solutions LLC

I need an edgier logo and business card designs. Current logo attached. I like the colors below. I would like the logo to incorporate a home in the design.
Title = Principal-Acquisitions
Email:KRVHOMESOLUTIONS@fernmail.example
555-214-0937
facebook
IG
2 sided business card with the front being contact info a slogan about selling a home fast. The back incorporating What we do. Buy houses, land, or commercial property as is. We find solutions to make the process of selling simple and fair.

Target Market(s)

Motivated house sellers.

Industry/Entity Type

Business

Contact Information for Business Card

Who we are: We are a Faith based Real Estate Investment Company. We pay cash for homes in any condition and can close quick. Whatever the reason you need to sell fast, we can help. We believe in creating win-win solutions to help you in your time of need. We care! We can help!

Logo Text

KRV Home Solutions LLC

Font styles to use
Sans Serif

Colors
33a6d7
0355a3
85abd2
cee9f5
9d9d9d
b2b2b2
ffffff

Requirements
Must have
• Old logo attached. I want something edgier.
• Company name, phone number, description on the back of what we can do. Pay all cash. Buy in as is condition. No fees,Commisions or closing costs.Close quick. No hassles with solutions to meet your unique situation.
• Call today for an offer within 24 hours.

```html
<!DOCTYPE html>
<html lang="en">
<head>
<meta charset="utf-8">
<title>KRV Home Solutions – Business Card</title>
<link href="https://fonts.googleapis.com/css2?family=Open+Sans:ital,wght@0,400;0,600;0,700;1,700&display=swap" rel="stylesheet">
<style>
  :root {
    --backdrop: #5a5a5a;
    --card-white: #f3f3f3;
    --navy: #1e3470;
    --ink: #2b2b2b;
    --on-navy: #ffffff;
  }
  * { margin: 0; padding: 0; box-sizing: border-box; }
  html, body {
    width: 1200px; height: 900px; overflow: hidden;
    background: var(--backdrop);
    font-family: "Open Sans", Arial, sans-serif;
  }
  .canvas { position: relative; width: 1200px; height: 900px; }

  .card {
    position: absolute; top: 200px; width: 310px; height: 502px;
    box-shadow: 3px 4px 8px rgba(0,0,0,0.45);
    overflow: hidden;
  }
  .card--front {
    left: 265px; background: var(--card-white);
    border-radius: 46px 0 46px 0;
  }
  .card--back {
    left: 641px; background: var(--navy);
    border-radius: 0 46px 0 46px;
  }

  /* front */
  .brand {
    position: absolute; top: 130px; left: 0; width: 100%;
    display: flex; align-items: center; justify-content: center; gap: 8px;
  }
  .brand__mark { width: 12px; height: 12px; background: var(--navy); }
  .brand__name {
    color: var(--navy); font-weight: 600; font-size: 19px;
  }
  .social {
    position: absolute; top: 205px; left: 0; width: 100%;
    display: flex; justify-content: center; gap: 9px;
  }
  .social__dot {
    width: 24px; height: 24px; border-radius: 50%;
    border: 1.5px solid var(--navy);
  }
  .contact { position: absolute; left: 26px; top: 382px; line-height: 1.3; }
  .contact__name {
    color: var(--navy); font-weight: 700; font-size: 19px; letter-spacing: 0.3px;
  }
  .contact__title { color: var(--ink); font-size: 13px; margin: 0 0 8px 1px; }
  .contact__line {
    display: flex; align-items: center; gap: 7px;
    color: var(--ink); font-size: 13px; margin-bottom: 2px;
  }
  .contact__line svg { width: 11px; height: 11px; fill: var(--navy); }

  /* back */
  .back-content {
    position: absolute; width: 502px; height: 310px;
    left: -96px; top: 96px;
    transform: rotate(-90deg);
    color: var(--on-navy);
  }
  .offer-list {
    position: absolute; top: 44px; left: 80px;
    list-style: none; font-size: 14.5px; font-weight: 600; line-height: 26px;
  }
  .offer-list li { padding-left: 13px; position: relative; white-space: nowrap; }
  .offer-list li::before {
    content: "★"; position: absolute; left: 0; font-size: 9px;
  }
  .offer-list .cont::before { content: none; }
  .divider {
    position: absolute; top: 232px; left: 92px; width: 325px;
    border-top: 1px solid rgba(255,255,255,0.8);
  }
  .cta {
    position: absolute; top: 247px; left: 22px; width: 440px;
    text-align: center; font-style: italic; font-weight: 700; font-size: 19px;
  }
</style>
</head>
<body>
<main class="canvas">
  <section class="card card--front">
    <div class="brand">
      <span class="brand__mark"></span>
      <span class="brand__name">KRV Home Solutions LLC</span>
    </div>
    <div class="social">
      <span class="social__dot"></span>
      <span class="social__dot"></span>
    </div>
    <div class="contact">
      <p class="contact__name">DANA REYES</p>
      <p class="contact__title">Managing Director</p>
      <p class="contact__line">
        <svg viewBox="0 0 24 24"><path d="M6.6 10.8a15.1 15.1 0 0 0 6.6 6.6l2.2-2.2a1 1 0 0 1 1-.25 11.4 11.4 0 0 0 3.6.57 1 1 0 0 1 1 1V20a1 1 0 0 1-1 1A17 17 0 0 1 3 4a1 1 0 0 1 1-1h3.5a1 1 0 0 1 1 1c0 1.25.2 2.45.57 3.57a1 1 0 0 1-.25 1z"/></svg>
        555-214-0937
      </p>
      <p class="contact__line">
        <svg viewBox="0 0 24 24"><path d="M2 5h20v14H2z"/><path d="M3 6l9 7 9-7" fill="none" stroke="#fff" stroke-width="1.6"/></svg>
        krvhomesolutions@fernmail.example
      </p>
    </div>
  </section>

  <section class="card card--back">
    <div class="back-content">
      <ul class="offer-list">
        <li>Buy houses, land or commercial property as is.</li>
        <li>Pay all cash.</li>
        <li>Buy in as is condition.</li>
        <li>No fees, commisions or closing costs.</li>
        <li>Close quick. No hassles with solutions</li>
        <li class="cont">to meet your unique situation.</li>
      </ul>
      <div class="divider"></div>
      <p class="cta">Call today for an offer within 24 hours.</p>
    </div>
  </section>
</main>
</body>
</html>
```